ultra-minimalist business card

front (black background, matte):

reza t. kovin
writer | photographer
get@rezakovin.com

back (white background, matte):

a picture speaks a thousand words;
a word draws a thousand pictures.

www.rezakovin.com

all text should be small (white or silver - as long as it shows against the black - on the front; black or gray - as long as it shows against the white - on the back).

feel free to get creative in terms of arrangement, alignment, and font type, but remember, the overall style is minimalist, so nothing too fancy, please.

thanks.

```html
<!DOCTYPE html>
<html lang="en">
<head>
<meta charset="utf-8">
<title>Reza T. Kovin — Business Card</title>
<link rel="stylesheet" href="https://fonts.googleapis.com/css2?family=Inter+Tight:wght@400;700;800&display=swap">
<style>
  :root {
    --backdrop: #d6cdd1;
    --card-dark: #0b0b0b;
    --card-light: #ffffff;
    --ink-light: #f4f4f2;
    --ink-light-soft: #bdbdba;
    --ink-dark: #111111;
    --ink-dark-soft: #777777;
  }
  * { margin: 0; padding: 0; box-sizing: border-box; }
  html, body {
    width: 1200px;
    height: 900px;
    overflow: hidden;
    background: var(--backdrop);
    font-family: "Inter Tight", "Helvetica Neue", Arial, sans-serif;
  }
  .canvas { position: relative; width: 1200px; height: 900px; }

  .card {
    position: absolute;
    width: 600px;
    height: 340px;
    overflow: hidden;
    box-shadow: 0 14px 28px rgba(0, 0, 0, 0.18);
  }
  .card--back { left: 90px; top: 80px; background: var(--card-light); color: var(--ink-dark); }
  .card--front { left: 510px; top: 480px; background: var(--card-dark); color: var(--ink-light); }

  /* Back: quote */
  .quote {
    position: absolute;
    left: 44px;
    top: 92px;
    font-weight: 700;
    font-size: 24px;
    line-height: 32px;
    letter-spacing: -0.02em;
    white-space: nowrap;
  }
  .quote__line { display: block; }

  .contact {
    position: absolute;
    right: 32px;
    bottom: 28px;
    display: flex;
    align-items: center;
    gap: 8px;
    font-size: 13px;
    font-weight: 400;
    letter-spacing: 0.01em;
    white-space: nowrap;
  }
  .card--back .contact { color: var(--ink-dark-soft); }
  .card--front .contact { color: var(--ink-light-soft); }
  .contact__icon { width: 14px; height: 14px; display: block; }

  /* Front: name */
  .identity {
    position: absolute;
    left: 44px;
    top: 120px;
  }
  .name {
    font-weight: 800;
    letter-spacing: -0.03em;
    white-space: nowrap;
    line-height: 1.05;
  }
  .name--first { font-size: 30px; }
  .name--last { font-size: 44px; }
  .role {
    margin-top: 12px;
    font-size: 13px;
    font-weight: 400;
    color: var(--ink-light-soft);
    letter-spacing: 0.02em;
    white-space: nowrap;
  }
</style>
</head>
<body>
<main class="canvas">

  <section class="card card--back" aria-label="Card back">
    <p class="quote">
      <span class="quote__line">a picture speaks</span>
      <span class="quote__line">a thousand words;</span>
      <span class="quote__line">a word draws</span>
      <span class="quote__line">a thousand pictures.</span>
    </p>
    <p class="contact contact--web">
      <svg class="contact__icon" viewBox="0 0 14 14" aria-hidden="true">
        <rect x="0.5" y="0.5" width="13" height="13" rx="2.5" fill="var(--ink-dark-soft)"/>
        <circle cx="7" cy="7" r="4" fill="none" stroke="var(--card-light)" stroke-width="1.1"/>
        <line x1="3" y1="7" x2="11" y2="7" stroke="var(--card-light)" stroke-width="1"/>
        <ellipse cx="7" cy="7" rx="1.8" ry="4" fill="none" stroke="var(--card-light)" stroke-width="1"/>
      </svg>
      www.rezakovin.com
    </p>
  </section>

  <section class="card card--front" aria-label="Card front">
    <div class="identity">
      <p class="name name--first">reza t.</p>
      <p class="name name--last">kovin</p>
      <p class="role">writer | photographer</p>
    </div>
    <p class="contact contact--mail">
      <svg class="contact__icon" viewBox="0 0 14 14" aria-hidden="true">
        <rect x="0.5" y="2.5" width="13" height="9" rx="1.5" fill="var(--ink-light-soft)"/>
        <polyline points="1.5,3.8 7,8 12.5,3.8" fill="none" stroke="var(--card-dark)" stroke-width="1.2"/>
      </svg>
      get@rezakovin.com
    </p>
  </section>

</main>
</body>
</html>
```